Business Card - connecting 2 souls and beggining the journey of self discovery

Logo on the front
with tag line

On the back list of services and contact details

Seminars
workshops
Coaching
podcasts

Darren Whitlow
Health & Wellbeing Life Coach
0491 372 615
darren@brightcoreliving.example
brightcoreliving.example

Industry/Entity Type

Life Coaching

Contact Information for Business Card

I like the use of colour from the logo to be used. I'm not a fan of white.

Requirements
Must have
• My tagline: The journey home starts with you
Nice to have
• Use of colour that is in the mind body soul logo

```html
<!DOCTYPE html>
<html lang="en">
<head>
<meta charset="utf-8">
<title>Brightcore Living – Business Card</title>
<link href="https://fonts.googleapis.com/css2?family=Open+Sans:ital,wght@0,400;0,600;0,700;1,400&display=swap" rel="stylesheet">
<style>
  :root {
    --backdrop: #171717;
    --sunflower: #fbd56b;
    --ink-grey: #6b6f7a;
    --paper: #fbf8f3;
    --charcoal: #4a4a4a;
    --rule: #555555;
    --text-dark: #3a3a3a;
    --gold: #f5c842;
    --white: #ffffff;
  }
  * { box-sizing: border-box; margin: 0; padding: 0; }
  html, body {
    width: 1200px; height: 1000px; overflow: hidden;
    background: var(--backdrop);
    font-family: "Open Sans", Arial, sans-serif;
  }
  .canvas {
    position: relative; width: 1200px; height: 1000px;
  }
  .card {
    position: absolute; width: 530px; height: 303px;
    box-shadow: 0 6px 18px rgba(0,0,0,.45);
    overflow: hidden;
  }
  /* Front */
  .card--front {
    left: 40px; top: 348px;
    background: var(--sunflower);
    display: flex; flex-direction: column; align-items: center; justify-content: center;
    color: var(--ink-grey);
  }
  .brand {
    display: flex; align-items: center; gap: 14px;
  }
  .brand__dot {
    width: 30px; height: 30px; border-radius: 50%;
    background: var(--ink-grey);
  }
  .brand__name {
    font-size: 34px; font-weight: 600; letter-spacing: -0.5px;
  }
  .tagline {
    margin-top: 8px; font-size: 17px; font-style: italic;
  }
  /* Back */
  .card--back {
    left: 630px; top: 348px;
    background: var(--paper);
  }
  .back__rule {
    position: absolute; left: 42px; top: 26px; width: 2px; height: 250px;
    background: var(--rule);
  }
  .contact {
    position: absolute; left: 70px; top: 82px; color: var(--text-dark);
  }
  .contact__name {
    font-size: 22px; font-weight: 700; color: var(--gold); line-height: 1.1;
  }
  .contact__role {
    font-size: 14px; margin-bottom: 14px;
  }
  .contact__list { list-style: none; }
  .contact__item {
    display: flex; align-items: center; gap: 8px; font-size: 14px; line-height: 1.45;
  }
  .contact__item svg { width: 12px; height: 12px; flex: none; }
  .services {
    position: absolute; right: 24px; top: 26px; width: 150px; height: 250px;
    background: var(--charcoal);
    list-style: none;
    display: flex; flex-direction: column; justify-content: center; gap: 22px;
    padding-left: 18px;
  }
  .services__item {
    color: var(--white); font-size: 16px; letter-spacing: 0.5px; text-transform: uppercase;
  }
</style>
</head>
<body>
<main class="canvas">
  <section class="card card--front" aria-label="Card front">
    <div class="brand">
      <span class="brand__dot"></span>
      <span class="brand__name">Brightcore Living</span>
    </div>
    <p class="tagline">“the journey home starts with you ”</p>
  </section>

  <section class="card card--back" aria-label="Card back">
    <span class="back__rule"></span>
    <div class="contact">
      <h1 class="contact__name">Darren Whitlow</h1>
      <p class="contact__role">Life Coach</p>
      <ul class="contact__list">
        <li class="contact__item">
          <svg viewBox="0 0 12 12" aria-hidden="true"><path d="M2.5 1l2 2.2-1 1.3c.6 1.4 1.6 2.4 3 3l1.3-1 2.2 2-1 1.8C5 10.5 1.5 7 .8 2z" fill="var(--gold)"/></svg>
          <span>0491 372 615</span>
        </li>
        <li class="contact__item">
          <svg viewBox="0 0 12 12" aria-hidden="true"><rect x="0.5" y="2" width="11" height="8" fill="var(--gold)"/><path d="M.5 2.5L6 6.5l5.5-4" stroke="var(--paper)" stroke-width="1" fill="none"/></svg>
          <span>darren@brightcoreliving.example</span>
        </li>
        <li class="contact__item">
          <svg viewBox="0 0 12 12" aria-hidden="true"><circle cx="6" cy="6" r="5" stroke="var(--gold)" stroke-width="1.2" fill="none"/><ellipse cx="6" cy="6" rx="2" ry="5" stroke="var(--gold)" stroke-width="1" fill="none"/><path d="M1 6h10" stroke="var(--gold)" stroke-width="1"/></svg>
          <span>www.brightcoreliving.example</span>
        </li>
      </ul>
    </div>
    <ul class="services">
      <li class="services__item">Seminars</li>
      <li class="services__item">Workshops</li>
      <li class="services__item">Coaching</li>
      <li class="services__item">Podcasts</li>
    </ul>
  </section>
</main>
</body>
</html>
```